New Website Design for PHOVAN.org

We are looking for a new website design for PHOVAN.org. PHOVAN is a non profit home inspector association based in California. Home Inspectors are people that come out and look at a house before it's purchased to let the buyer know of any defects that may exist.
Our site is based on Joomla so if you'll be able to make a Joomla 3 template as well, please let us know (not required, but a bonus).
We would like to see designs that incorporate royal blue, white and chrome into the site as that's our main business colors.
We would like a place for rotating banners though they don't need to be the same size as the current site.
We would like navigation to be easier to manage with menus only across the top (via drop down menus) where we are going to sort out the items currently on the side. Possibly the front page could have a graphic link to separate portals for Realtors, Home Buyers and Inspectors, but that's just one option.
We would like a good mobile design or something that will scale easily to mobile.
The Find an Inspector feature is important and should stand out. The ASK PHOVANr site
Current home page feels a bit busy. Would like to simplify a bit.

```html
<!DOCTYPE html>
<html lang="en">
<head>
<meta charset="utf-8">
<title>PHOVAN – Pacific Home Inspection Association</title>
<link rel="stylesheet" href="https://fonts.googleapis.com/css2?family=Roboto:wght@300;400;500;700&family=Roboto+Condensed:wght@400&family=Ubuntu:wght@400;500&display=swap">
<style>
:root{
  --royal:#2e4a9a;
  --royal-dark:#1f3a85;
  --royal-band:#3a56a5;
  --ink:#333;
  --muted:#8a8a8a;
  --page:#f1f1f1;
  --line:#3b3b3b;
  --footer-top:#2b2b2b;
  --footer-bottom:#141414;
  --footer-text:#d6d6d6;
  --olive:#3a3520;
}
*{box-sizing:border-box;margin:0;padding:0}
html,body{width:995px;height:1200px;overflow:hidden}
body{position:relative;background:var(--page);font-family:"Roboto",sans-serif;color:var(--ink)}
.abs{position:absolute}

/* header */
.site-header{left:0;top:0;width:995px;height:122px;background:linear-gradient(#fff,#ececec);border-top:2px solid #222;border-bottom:2px solid var(--royal)}
.login-tab{left:749px;top:0;width:119px;height:27px;background:var(--royal-dark);color:#fff;font:500 13px/27px "Ubuntu",sans-serif;text-align:center;border-radius:0 0 5px 5px}
.brand-mark{left:115px;top:19px;width:86px;height:86px;border-radius:50%;background:#fff;border:4px solid var(--royal-dark)}
.brand-name{left:219px;top:43px;font:400 20px/24px "Ubuntu",sans-serif;color:#222}
.support-icon{left:728px;top:52px}
.support{left:777px;top:51px;font:400 17px/20px "Ubuntu",sans-serif;color:#222}
.support b{display:block;font-weight:400;font-size:13.5px;line-height:17px;margin-top:2px}
.main-nav{left:0;top:122px;width:995px;height:48px;background:linear-gradient(#fafafa,#ececec);border-bottom:1px solid #ddd}
.main-nav ul{list-style:none;display:flex;position:absolute;left:111px;top:15px}
.main-nav li{font:400 12px/16px "Ubuntu",sans-serif;color:var(--royal)}
.main-nav li+li{margin-left:41px}

/* hero */
.hero{left:91px;top:185px;width:813px;height:282px;background:linear-gradient(90deg,#f4f4f6 0%,#eeeff2 50%,#d9dbe2 100%);border:1px solid #dcdcdc;border-bottom:none}
.hero-photo{left:497px;top:185px;width:407px;height:282px;background:linear-gradient(120deg,#e8e6e1 0%,#d4d0c8 40%,#6f7d98 70%,#3f4c6b 100%)}
.hero-title{left:116px;top:227px;width:390px;font:700 25px/26px "Roboto",sans-serif;letter-spacing:-1px;color:var(--royal)}
.hero-sub{left:116px;top:287px;font:400 13.3px/18px "Roboto",sans-serif;color:#444}
.hero-text{left:116px;top:314px;width:380px;font:300 10.8px/17px "Roboto",sans-serif;color:var(--muted)}
.btn-learn{left:117px;top:394px;width:128px;height:31px;border-radius:4px;background:linear-gradient(#3b58ae,#223e8c);border:1px solid #1a2f6e;color:#fff;font:500 14px/29px "Ubuntu",sans-serif;text-align:center}
.hero-rule{left:91px;top:466px;width:813px;height:3px;background:var(--line)}
.portal{width:160px;text-align:center}
.portal svg{display:block;margin:0 auto}
.portal span{display:block;margin-top:7px;font:400 15px/18px "Roboto Condensed",sans-serif;color:var(--royal)}
.portal.dark span{color:#222}

/* welcome */
.welcome{left:91px;top:565px;width:813px;height:184px;background:linear-gradient(#f6f6f6,#ececec);border:1px solid #d8d8d8;border-radius:6px;overflow:hidden}
.welcome-bar{height:35px;background:var(--royal-band);color:#fff;font:500 13.5px/35px "Ubuntu",sans-serif;padding-left:17px}
.welcome h2{position:absolute;left:17px;top:52px;font:400 14px/18px "Roboto",sans-serif;color:#222}
.welcome p{position:absolute;left:17px;top:76px;width:572px;font:300 11px/19px "Roboto",sans-serif;color:var(--muted)}
.welcome-photo{left:603px;top:56px;width:195px;height:112px;background:linear-gradient(135deg,#4a3a2c,#b7865a 45%,#8a5c38 70%,#3e3026)}

/* info band */
.info-band{left:91px;top:770px;width:813px;height:169px;background:var(--royal-band)}
.info-band h3{position:absolute;top:20px;font:500 13.5px/16px "Ubuntu",sans-serif;color:#fff}
.news{left:30px;top:47px;width:240px;color:#fff}
.news li{list-style:none;font:400 10px/13px "Roboto",sans-serif;margin-bottom:9px}
.news small{display:block;font-size:9px}
.search-copy{left:291px;top:47px;width:220px;font:400 10px/15px "Roboto",sans-serif;color:#fff}
.zip{left:289px;top:91px;width:234px;height:25px;background:#fff;border:1px solid #cfd4e4;font:300 11px/23px "Roboto",sans-serif;color:#999;padding-left:9px}
.btn-signup{left:289px;top:128px;width:67px;height:21px;background:var(--olive);border:1px solid #1c1a10;border-radius:3px;color:#fff;font:400 11px/19px "Roboto",sans-serif;text-align:center}
.quote{left:553px;width:240px;color:#fff}
.quote .avatar{position:absolute;left:0;top:0;width:48px;height:45px;background:linear-gradient(#e9e2da,#9b8c80)}
.quote .name{position:absolute;left:57px;top:0;font:400 10px/12px "Roboto",sans-serif}
.quote .line{position:absolute;left:57px;top:16px;width:176px;font:400 9px/14px "Roboto",sans-serif}
.quote .date{float:right}

/* footer */
.site-footer{left:0;top:962px;width:995px;height:238px;background:linear-gradient(var(--footer-top),var(--footer-bottom));color:var(--footer-text)}
.site-footer h4{position:absolute;font:400 17px/20px "Ubuntu",sans-serif;color:#eee}
.map{left:109px;top:62px;width:252px;height:126px;background:linear-gradient(135deg,#d9dcc8,#ece9d6 50%,#cdd4bf)}
.signup-panel{left:395px;top:61px;width:200px;height:94px;background:#232323}
.rule{height:1px;background:#555}
.footer-list{list-style:none;font:400 10px/17px "Roboto",sans-serif}
.email-copy{left:404px;top:72px;width:190px;font:400 10px/14px "Roboto",sans-serif}
.email-field{left:404px;top:112px;width:181px;height:18px;background:#ddd;border:1px solid #888;font:400 9.5px/16px "Roboto",sans-serif;color:#555;padding-left:5px}
.email-field b{position:absolute;right:3px;top:2px;width:26px;height:12px;background:#222;color:#fff;font:700 7px/12px "Roboto",sans-serif;text-align:center;border-radius:2px}
.social{top:155px;width:30px;height:30px;border-radius:50%;background:#fff;color:#111;font:500 7px/30px "Roboto",sans-serif;text-align:center}
.legal{left:109px;top:211px;font:400 10.4px/13px "Roboto",sans-serif;color:#ddd}
.footer-links{left:591px;top:211px;display:flex;gap:16px;font:400 10.4px/13px "Roboto",sans-serif;color:#ddd;list-style:none}
</style>
</head>
<body>

<header class="abs site-header">
  <div class="abs login-tab">Inspector Login</div>
  <div class="abs brand-mark" aria-hidden="true"></div>
  <div class="abs brand-name">Pacific Home Inspection<br>Association</div>
  <svg class="abs support-icon" width="40" height="40" viewBox="0 0 40 40" aria-hidden="true">
    <path d="M6 22a14 14 0 0 1 28 0" fill="none" stroke="#333" stroke-width="3"/>
    <rect x="3" y="20" width="7" height="12" rx="3" fill="#333"/>
    <rect x="30" y="20" width="7" height="12" rx="3" fill="#333"/>
    <path d="M33 32q0 6-10 6" fill="none" stroke="#333" stroke-width="2"/>
    <rect x="18" y="35" width="7" height="4" rx="2" fill="var(--royal)"/>
  </svg>
  <div class="abs support">Live Support<b>1-800-555-0142</b></div>
</header>

<nav class="abs main-nav">
  <ul>
    <li>Home</li><li>Find an Inspector</li><li>Home Buyers &amp; Sellers</li><li>Real Estate Agents</li><li>Inspectors</li><li>Ask PHOVAN</li><li>Conferences</li>
  </ul>
</nav>

<section class="abs hero"></section>
<div class="abs hero-photo" role="img" aria-label="Smiling home inspector on a yellow ladder beside white house siding"></div>
<h1 class="abs hero-title">Lorem Ipsum est simplement du faux texte employé dans la sition.</h1>
<p class="abs hero-sub">Survivre cinq siècles, mais s'est aussi adapté</p>
<p class="abs hero-text">Lorem Ipsum est simplement du faux texte employé dans la sition et la misen page avant impression. Le Lorem Ipsum est le faux texte standard de l'imprimerie depuis les années 1500, quand un peintre anonyme assembla ensemble.</p>
<div class="abs btn-learn">Learn More</div>
<div class="abs hero-rule"></div>

<div class="abs portal" style="left:155px;top:439px">
  <svg width="54" height="62" viewBox="0 0 54 62" aria-hidden="true">
    <polygon points="27,1 53,16 53,46 27,61 1,46 1,16" fill="var(--royal-dark)"/>
    <path d="M13 30 27 19 41 30" fill="none" stroke="#fff" stroke-width="3"/>
    <rect x="16" y="30" width="22" height="14" fill="#fff"/>
    <circle cx="31" cy="38" r="3.5" fill="var(--royal-dark)"/>
  </svg>
  <span>HOME BUYER</span>
</div>
<div class="abs portal dark" style="left:417px;top:439px">
  <svg width="54" height="62" viewBox="0 0 54 62" aria-hidden="true">
    <polygon points="27,1 53,16 53,46 27,61 1,46 1,16" fill="#2a2a2a"/>
    <path d="M13 30 27 19 41 30" fill="none" stroke="#fff" stroke-width="3"/>
    <rect x="16" y="30" width="22" height="14" fill="#fff"/>
    <circle cx="29" cy="38" r="4" fill="none" stroke="#2a2a2a" stroke-width="2"/>
    <line x1="32" y1="41" x2="36" y2="44" stroke="#2a2a2a" stroke-width="2"/>
  </svg>
  <span>HOME INSPECTOR</span>
</div>
<div class="abs portal" style="left:679px;top:439px">
  <svg width="54" height="62" viewBox="0 0 54 62" aria-hidden="true">
    <polygon points="27,1 53,16 53,46 27,61 1,46 1,16" fill="var(--royal-dark)"/>
    <path d="M13 30 27 19 41 30" fill="none" stroke="#fff" stroke-width="3"/>
    <rect x="16" y="30" width="22" height="14" fill="#fff"/>
    <rect x="20" y="33" width="14" height="8" fill="none" stroke="var(--royal-dark)" stroke-width="1.5"/>
  </svg>
  <span>HOME REALTOR</span>
</div>

<section class="abs welcome">
  <div class="welcome-bar">WELCOME TO PACIFIC HOME INSPECTION ASSOCIATION</div>
  <h2>Dolore eu feugiat nulla facilisis at vero eros et accumsan et iusto odio.</h2>
  <p>Lorem Ipsum est simplement du faux texte employé dans la sition et la misen page avant impression. Le Lorem Ipsum est le faux texte standard de l'imprimerie depuis les années 1500, quand un peintre anonyme assembla ensemble des morceaux de texte pour réaliser un livre spécimen de polices de texte. Il n'a pas fait que Il a été popularisé danles années 1960 grâce lasurvivre cinq siècles, mais s'est aussi adapté bureautique informatique, sans que son contenu n'en soit modifié. Popularisé dans les années 1960.</p>
  <div class="abs welcome-photo" role="img" aria-label="Close-up of a hammer driving a nail into wood"></div>
</section>

<section class="abs info-band">
  <h3 style="left:30px">NEWS &amp; EVENTS</h3>
  <ul class="abs news">
    <li>Praesent luptatum ril delenit augue duis dolore<small>Yesterday at 08:23:14 PM</small></li>
    <li>Praesent luptatum ril delenit augue duis dolore<small>Yesterday at 07:58:35 PM</small></li>
    <li>Praesent luptatum ril delenit augue duis dolore<small>Yesterday at 07:11:19 PM</small></li>
  </ul>
  <h3 style="left:291px">SEARCH FOR INSPECTOR</h3>
  <p class="abs search-copy">Lorem Ipsum est simplement du faux texte employé dans.</p>
  <div class="abs zip">Enter your Zip Code</div>
  <div class="abs btn-signup">Sign Up</div>
  <h3 style="left:553px">TESTIMONIALS</h3>
  <div class="abs quote" style="top:45px">
    <div class="avatar" role="img" aria-label="Portrait photo of a client"></div>
    <div class="name">Marlow Bennett</div>
    <div class="line">On sait depuis longtemps que travailler avec du texte lisibale <span class="date">14-12-2012</span></div>
  </div>
  <div class="abs quote" style="top:109px">
    <div class="avatar" role="img" aria-label="Portrait photo of a client"></div>
    <div class="name">Marlow Bennett</div>
    <div class="line">On sait depuis longtemps que travailler avec du texte lisibale <span class="date">14-12-2012</span></div>
  </div>
</section>

<footer class="abs site-footer">
  <h4 style="left:106px;top:28px">Find a Home Inspector</h4>
  <div class="abs map" role="img" aria-label="Street map of the local area"></div>

  <div class="abs signup-panel"></div>
  <h4 style="left:401px;top:28px">Email Signup</h4>
  <div class="abs rule" style="left:401px;top:61px;width:187px"></div>
  <p class="abs email-copy">Click here to create your account as a Real Estate Agent.</p>
  <div class="abs email-field">Enter your email<b>GO</b></div>
  <div class="abs rule" style="left:401px;top:144px;width:187px"></div>
  <div class="abs social" style="left:414px">Share</div>
  <div class="abs social" style="left:457px">Post</div>
  <div class="abs social" style="left:500px">Link</div>
  <div class="abs social" style="left:543px">Plus</div>

  <h4 style="left:630px;top:30px">Get Help</h4>
  <div class="abs rule" style="left:630px;top:61px;width:108px"></div>
  <ul class="abs footer-list" style="left:630px;top:69px">
    <li>Lorem ipsum dolor sit</li><li>Lorem ipsum dolor sit</li><li>Lorem ipsum dolor sit</li>
  </ul>

  <h4 style="left:778px;top:30px">Sitemap</h4>
  <div class="abs rule" style="left:778px;top:61px;width:108px"></div>
  <ul class="abs footer-list" style="left:778px;top:69px">
    <li>Lorem ipsum dolor sit</li><li>Lorem ipsum dolor sit</li><li>Lorem ipsum dolor sit</li><li>Lorem ipsum dolor sit</li>
  </ul>

  <p class="abs legal">Pacific Home Inspection Association. All Rights Reserved</p>
  <ul class="abs footer-links"><li>Testimonials</li><li>Tutorials</li><li>Message Boards</li><li>Help Desk</li></ul>
</footer>

</body>
</html>
```